Systems and Technology Consultants - Website

Design & Build a website for a new company which operates in the Systems and Technology space for Transportation, Government and Commercial sectors.

Overall design should be minimalist in nature.
Should also have a feed that provides news and event updates on the main page.
Logo has already been awarded and should be incorporated into the site.

We like the overall layout, functionality and simplicity of the below sites. Submitted designs could be similar to or a combination of the aspects on these sites, or perhaps a whole different concept - we are open to new ideas.
Norvique.com
Teblo.it

Update 1 Dated 27 May 2014

All I am moving away from the Teblo.it website and would like it to be more aligned with Norvique.com not only in layout but in functionality. I will be extending the deadline of this design brief for two weeks to incorporate additional requirements and will add addtional funding to the project.

Apologies for not having more information available to provide but with so many submissions its getting confusing.

Thanks Derek

Please note that the brief has been updated and the deadline has been extended.

Important: We will need two language versions of the website, English and Arabic; the website is hosted on HostPelican

Hello All, Thank you for your submissions. We have narrowed it down to the final 6 designers and I just wanted to take a moment and provide a bit of feedback regarding the concepts that we like and the modifications we are looking for. First, let me mention some of the design functions we like. - At the top of the homepage we really like the "region" or "language" tab so that the website can be viewed in both English and Arabic. - We like the homepage to have clear color variation so that the different sections of the homepage are distinct. Additionally, we like the bottom portion of the homepage to be in red. We feel that draws attention to our contact information. Again, we would like the colors to integrate black, gray-scale, red, etc. - Having a search tab at the top of the home page, or integrated into the main image, so that the site is easy to navigate. - We especially like the main image to have the scrolling tabs at the bottom so it is easy to browse the services offered (Consultancy, Solutions Architecture, Masters Systems Integration, Independent Design Review). - In regards to the services offered tab we really like the idea that a few people presented that have the outside of our logo with an icon in the middle of consultancy, solutions, etc., etc. Secondly, as mentioned in our brief we really enjoy the design of norvique site. Specially, we enjoy the strong iconic images they use, the way the tabs at the top scroll easily, and contact us page that generates an email. Lastly, I've included some photos of the concept we have been working on. What we are trying to demonstrate is how our company offers a range of services that are essentially linked together. We provide individual services that when combined present the full service package. We would like this concept to be integrated into the over concept of our website. Please feel free to ask for clarification of any of the above points or contact us if you have any additional questions. We appreciate all of your hard work and are very excited to see the updated designs. Best, Marta Vennick Quelbrant Senior Program Manager marta.vennick@quelbrant-example.com

Industry/Entity Type

Government

Font styles to use
Serif
Sans Serif

Requirements
Must have
• Must work on/adapt to various/mobile devices (responsive)
Must be simple and straightforward
Colors should be in line/matching with logo
2 language versions: English and Arabic (no Thai)
Services should be the first group/row of items after/below the main image
Note: the website will be hosted by hostpelican
Nice to have
• Submit feedback form
What's New section
The banner at the bottom of the site should not be too large; we would like a narrow one more
It would be nice if the header/top banner (with Home, About, etc. tabs) could stay in place as you scroll down (like Norvique and Chatterloop)
We will likely only use one image with a Company slogan on the Home page rather than a carousel of images to rotate through
Should not have
• This is the existing website: http://www.quelbrant-example.org
We do not like the animation, the way the banner icons/titles bounce
Not simple enough, we don't like the functionality or how pages load so slowly
We do not like the logo centered - it should be at the left
The banner and its tabs should not be towards the right, we would like them to be centered, to go all the way across and to be below the logo

```html
<!DOCTYPE html>
<html lang="en">
<head>
<meta charset="utf-8">
<title>Quelbrant – Home</title>
<link href="https://fonts.googleapis.com/css2?family=Open+Sans:wght@300;400;600;700&display=swap" rel="stylesheet">
<style>
:root{
  --red:#e5202a;
  --orange:#f79a12;
  --ink:#2b2b2b;
  --text:#444;
  --muted:#8a8a8a;
  --panel:#f1f0f0;
  --dark:#2a2a2a;
  --darker:#1d1d1d;
  --hero-a:#061018;
  --hero-b:#0f3a4e;
  --hero-c:#3f9fb8;
}
*{margin:0;padding:0;box-sizing:border-box}
html,body{width:718px;height:1200px;overflow:hidden;background:#fff}
body{font-family:"Open Sans",Arial,sans-serif;color:var(--text);position:relative}
.abs{position:absolute}

.topbar{left:0;top:0;width:718px;height:15px;background:var(--ink);color:#fff;font-size:7.5px;line-height:15px}
.topbar .links{left:67px}
.topbar .links span{margin:0 5px;color:#aaa}
.topbar .contact{right:65px;display:flex;gap:20px;align-items:center}
.topbar .contact span{display:flex;align-items:center;gap:4px}

.brand{left:67px;top:37px;display:flex;align-items:center;gap:6px;font-size:12px;font-weight:700;color:var(--red);letter-spacing:1.5px}
.brand i{display:block;width:9px;height:9px;background:var(--red)}
.search{left:485px;top:25px;width:168px;height:19px;border:1px solid #ddd;background:#f3f3f3;border-radius:2px}
.search svg{position:absolute;right:8px;top:4px}
.nav{top:73px;left:0;width:718px;font-size:8.8px;color:#222}
.nav a{position:absolute;color:inherit;text-decoration:none;white-space:nowrap}
.nav .active{color:var(--red)}
.nav .active::after{content:"";position:absolute;left:-6px;right:-6px;top:15px;height:2px;background:var(--red)}

.hero{left:0;top:102px;width:718px;height:298px;background:linear-gradient(90deg,var(--hero-a) 0%,var(--hero-a) 30%,var(--hero-b) 62%,var(--hero-c) 80%,var(--hero-b) 100%)}
.hero-copy{left:66px;top:187px;font-size:14px;line-height:16.7px;color:#fff;font-weight:400;white-space:nowrap}
.hero-copy b{color:var(--red);font-weight:700}
.btn-hero{left:65px;top:271px;width:72px;height:21px;background:var(--orange);color:#fff;font-size:9.5px;font-weight:600;text-align:center;line-height:21px}
.hero-shadow{left:20px;top:400px;width:678px;height:14px;background:radial-gradient(ellipse at top,rgba(0,0,0,.22),rgba(0,0,0,0) 70%)}

.section-title{left:0;width:718px;top:436px;text-align:center;font-size:14px;font-weight:400;color:#333}
.section-title span{text-decoration:underline;text-underline-offset:3px;text-decoration-thickness:1px}

.service{top:475px;width:180px;text-align:center}
.service .icon{width:58px;height:58px;border-radius:50%;margin:6px auto 0}
.service h3{font-size:11px;font-weight:400;color:#222;margin-top:17px}
.service p{font-size:7.2px;line-height:12px;color:var(--muted);margin-top:12px;padding:0 6px}
.service .btn{display:inline-block;margin-top:16px;width:54px;height:18px;line-height:16px;border:1.5px solid #333;font-size:7.2px;color:#222}
.service.first .btn{border-color:var(--red);color:var(--red)}
.divider{top:490px;width:1px;height:175px;background:linear-gradient(#fff,#eee,#fff)}
.sep{left:80px;top:697px;width:560px;height:1px;background:linear-gradient(90deg,#fff,#eee,#fff)}

.block-title{top:720px;font-size:12px;font-weight:400;color:#333}
.acc-open{left:77px;top:747px;width:276px;height:133px;background:var(--panel)}
.acc-open .bar{position:absolute;left:0;top:0;width:24px;height:133px;background:#d9d8d8}
.acc-open .toggle{position:absolute;left:0;top:0;width:24px;height:34px;background:var(--red)}
.acc-open .toggle::after{content:"";position:absolute;left:8px;top:16px;width:8px;height:1px;background:#fff}
.acc-open h4{position:absolute;left:33px;top:11px;width:210px;font-size:9px;font-weight:400;line-height:11px;color:#222}
.acc-open p{position:absolute;left:33px;top:44px;width:236px;font-size:7.2px;line-height:12px;color:var(--muted)}
.acc{left:77px;width:276px;background:var(--panel);font-size:8px;color:#222}
.acc .toggle{position:absolute;left:0;top:0;width:24px;height:100%;background:#3a3a3a}
.acc .toggle::before,.acc .toggle::after{content:"";position:absolute;left:7px;top:50%;width:10px;height:1.3px;background:#fff}
.acc .toggle::after{transform:rotate(90deg)}
.acc span{position:absolute;left:32px;top:50%;transform:translateY(-50%);white-space:nowrap}

.news{left:391px;width:255px}
.date{position:absolute;left:0;top:0;width:37px;height:34px}
.date .d{height:19px;background:#3a3a3a;color:#fff;font-size:13px;text-align:center;line-height:20px}
.date .m{height:15px;background:var(--red);color:#fff;font-size:11px;text-align:center;line-height:14px}
.news h5{position:absolute;left:43px;top:-3px;font-size:9px;font-weight:400;color:#222}
.news p{position:absolute;left:43px;top:11px;width:212px;font-size:7.2px;line-height:12px;color:var(--muted)}

.footer{left:0;top:1012px;width:718px;height:153px;background:var(--dark)}
.f-col{top:1029px}
.f-col h6{font-size:11px;font-weight:400;color:#fff;margin-bottom:8px}
.f-col p,.f-col li{font-size:7.5px;line-height:12px;color:#9a9a9a;list-style:none}
.f-col li{color:#d5d5d5}
.map{left:498px;top:1055px;width:155px;height:99px;background:linear-gradient(135deg,#e9e5dc,#d8d3c6)}
.copyright{left:0;top:1165px;width:718px;height:35px;background:var(--darker);color:#ddd;font-size:7.5px;text-align:center;line-height:35px}
</style>
</head>
<body>

<div class="abs topbar">
  <div class="abs links">Terms<span>|</span>Privacy Policy</div>
  <div class="abs contact">
    <span><svg width="7" height="7" viewBox="0 0 10 10"><path d="M2 0l2 2.5-1 1.3c.6 1.3 1.6 2.3 2.9 2.9L7.2 5.7 10 7.6 8.7 10C4 9.5.4 5.9 0 1.2z" fill="#fff"/></svg>+100 555 0142</span>
    <span><svg width="9" height="7" viewBox="0 0 12 9"><rect x=".5" y=".5" width="11" height="8" fill="none" stroke="#fff"/><path d="M.5.5 6 5l5.5-4.5" fill="none" stroke="#fff"/></svg>info@quelbrant-example.com</span>
  </div>
</div>

<div class="abs brand"><i></i>QUELBRANT</div>
<div class="abs search"><svg width="10" height="10" viewBox="0 0 10 10"><circle cx="4" cy="4" r="3" fill="none" stroke="#111" stroke-width="1.5"/><path d="M6.2 6.2 9 9" stroke="#111" stroke-width="1.8"/></svg></div>
<nav class="abs nav">
  <a class="active" style="left:276px">HOME</a>
  <a style="left:332px">Business Units</a>
  <a style="left:419px">Services</a>
  <a style="left:480px">About Us</a>
  <a style="left:545px">Locations</a>
  <a style="left:610px">Contact Us</a>
</nav>

<div class="abs hero" role="img" aria-label="Photo of a businessman in a suit drawing glowing technology diagrams on a dark screen"></div>
<div class="abs hero-copy"><b>QUELBRANT</b> Specializes in delivering<br>quality Professional Services and Techni-<br>cal Projects that Support<br>larger Business goals.</div>
<div class="abs btn-hero">Read More</div>
<div class="abs hero-shadow"></div>

<h2 class="abs section-title"><span>Our Services</span></h2>

<div class="abs service first" style="left:72px">
  <div class="icon" role="img" aria-label="Consulting icon" style="background:var(--red)"></div>
  <h3>Consulting</h3>
  <p>Lorem Ipsum is simply dummy text of the printing and typesetting industry. Lorem Ipsum has been the industry's standard dummy text ever since the 1500s.</p>
  <span class="btn">Read More</span>
</div>
<div class="abs divider" style="left:262px"></div>
<div class="abs service" style="left:267px">
  <div class="icon" role="img" aria-label="Engineering icon" style="background:#cfcfcf"></div>
  <h3>Engineering</h3>
  <p>Lorem Ipsum is simply dummy text of the printing and typesetting industry. Lorem Ipsum has been the industry's standard dummy text ever since the 1500s.</p>
  <span class="btn">Read More</span>
</div>
<div class="abs divider" style="left:456px"></div>
<div class="abs service" style="left:458px">
  <div class="icon" role="img" aria-label="Construction icon" style="background:#cfcfcf"></div>
  <h3>Construction</h3>
  <p>Lorem Ipsum is simply dummy text of the printing and typesetting industry. Lorem Ipsum has been the industry's standard dummy text ever since the 1500s.</p>
  <span class="btn">Read More</span>
</div>
<div class="abs sep"></div>

<h3 class="abs block-title" style="left:78px">Articles</h3>
<div class="abs acc-open">
  <div class="bar"></div><div class="toggle"></div>
  <h4>Lorem ipsum dolor sit amet, consectetur adipisicing elit</h4>
  <p>Lorem Ipsum is simply dummy text of the printing and typesetting industry. Lorem Ipsum has been the industry's standard dummy text ever since the 1500s, when an unknown printer took a galley of type and scrambled it to make a type specimen book. It has survived not only five centuries, but also the leap into electronic typesetting, remaining essentially unchanged. It was popularised in the 1960s.</p>
</div>
<div class="abs acc" style="top:885px;height:25px"><div class="toggle"></div><span>Lorem ipsum dolor sit amet, consectetur adipisicing elit</span></div>
<div class="abs acc" style="top:915px;height:25px"><div class="toggle"></div><span>Lorem ipsum dolor sit amet,</span></div>
<div class="abs acc" style="top:946px;height:34px"><div class="toggle"></div><span>Lorem ipsum dolor sit amet, consectetur adipisicing elit</span></div>

<h3 class="abs block-title" style="left:391px">News</h3>
<div class="abs news" style="top:748px"><div class="date"><div class="d">27</div><div class="m">Feb</div></div><h5>Lorem ipsum dolor sit amet,</h5><p>Lorem Ipsum is simply dummy text of the printing and typesetting industry</p></div>
<div class="abs news" style="top:810px"><div class="date"><div class="d">23</div><div class="m">Feb</div></div><h5>Lorem ipsum dolor sit amet,</h5><p>Lorem Ipsum is simply dummy text of the printing and typesetting industry.</p></div>
<div class="abs news" style="top:872px"><div class="date"><div class="d">22</div><div class="m">Feb</div></div><h5>Lorem ipsum dolor sit amet,</h5><p>Lorem Ipsum is simply dummy text of the printing and typesetting industry. Lorem Ipsum has been the industry's standard dummy text</p></div>
<div class="abs news" style="top:937px"><div class="date"><div class="d">23</div><div class="m">Feb</div></div><h5>Lorem ipsum dolor sit amet,</h5><p>Lorem Ipsum is simply dummy text of the printing and typesetting industry.</p></div>

<footer class="abs footer"></footer>
<div class="abs f-col" style="left:67px;width:135px"><h6>What We do</h6><p>Lorem Ipsum is simply dummy text of the printing and typesetting industry. Lorem Ipsum has been the industry's standard dummy text ever since the 1500s.when an unknown printer took a galley of type and scrambled it to make a type specimen book.</p></div>
<div class="abs f-col" style="left:233px"><h6>Site Map</h6><ul><li>Home</li><li>Business Units</li><li>Services</li><li>About Us</li><li>Locations</li><li>Contact Us</li></ul></div>
<div class="abs f-col" style="left:361px"><h6>Get in touch</h6><p style="color:#c8c8c8">Toll-Free: 1-800-555-0199<br>Local: 555-013-2846<br>Fax: 555-013-2847</p></div>
<div class="abs f-col" style="left:504px"><h6>Map</h6></div>
<div class="abs map" role="img" aria-label="Street map showing the office location"></div>
<div class="abs copyright">Copyright © 2014 Quelbrant . All rights reserved.</div>

</body>
</html>
```